Homepage Website Design for luxury picnic company

We need a homepage designed for a luxury picnic business to match our updated branding/logo which we're currently completing on PixelHarbor with another competition. Please see attached logo/colour example to use for now.

PLEASE NOTE: We are only after graphic design concepts as part of this competition. I will get another developer to actually code the website.

It is important that this website is very elegant/luxurious and stands out from a visual perspective. The images really need to match the content/sections also. The new branding colours are silver with a dark background. Please create the new website homepage to match these colours/branding.

Please create as many concepts as possible and then I will provide feedback from there

The website content including sections is here https://files.quorvanta.com/doc/d/7kRmWp2QxLn9TfBv4ZsYh3JcA8eGuD5oNiKtE1rVbXq/view?mode=share

Images to use are located here https://store.quorvanta.com/vault/folders/9HwTnK4-MzPa2RbE73-VyxLqJdsfGoUe?mode=share and there is also lots of videos at this link which you can screenshot images out of if needed https://www.boxtelmo.net/sh/k827rvwd3mjq8t2/ZZQmnx4RtUe7hWLP9C5dvkXbN?dl=0

Any questions please contact me

1 page

```html
<!DOCTYPE html>
<html lang="en">
<head>
<meta charset="utf-8">
<title>Ridgeline Picnics — Home</title>
<link href="https://fonts.googleapis.com/css2?family=Arimo:wght@400;700&family=Cormorant+Garamond:wght@500&display=swap" rel="stylesheet">
<style>
  :root {
    --navy: #0b0e1a;
    --silver: #e6e7ea;
    --white: #ffffff;
    --ink: #111111;
    --grey-shadow: rgba(0,0,0,0.16);
    --badge: rgba(255,255,255,0.18);
  }
  * { box-sizing: border-box; margin: 0; padding: 0; }
  html, body { width: 1200px; height: 3092px; overflow: hidden; }
  body { position: relative; background: var(--white); font-family: "Arimo", Helvetica, Arial, sans-serif; color: var(--ink); }
  .abs { position: absolute; }

  /* Header */
  .site-header { left: 0; top: 0; width: 1200px; height: 100px; background: var(--navy); }
  .brand { left: 48px; top: 30px; display: flex; align-items: center; gap: 10px; color: var(--silver);
           font-family: "Cormorant Garamond", Georgia, serif; font-size: 28px; font-weight: 500; }
  .brand-dot { width: 14px; height: 14px; border-radius: 50%; background: var(--silver); }
  .main-nav { right: 50px; top: 36px; display: flex; gap: 29px; }
  .main-nav a { color: var(--silver); text-decoration: none; font-size: 22px; letter-spacing: 0.2px; padding-bottom: 4px; }
  .main-nav a.is-active { border-bottom: 2px solid var(--silver); }

  /* Hero */
  .hero { left: 0; top: 100px; width: 1200px; height: 600px;
          background:
            radial-gradient(ellipse 420px 300px at 600px 420px, rgba(40,40,46,0.55), transparent 70%),
            linear-gradient(180deg, #9a948c 0%, #55606a 18%, #43504a 40%, #6b5a40 58%, #5e4a44 76%, #8b7468 100%); }
  .hero-title { left: 0; top: 350px; width: 1200px; text-align: center; color: var(--white); font-weight: 700; font-size: 31px; }
  .hero-sub { left: 0; top: 402px; width: 1200px; text-align: center; color: var(--white); font-size: 21px; }
  .hero-btn { left: 450px; top: 475px; width: 300px; height: 48px; border-radius: 24px; background: var(--navy);
              color: var(--silver); font-size: 22px; display: flex; align-items: center; justify-content: center; }
  .safe-badge { left: 996px; top: 495px; width: 152px; height: 152px; border-radius: 50%;
                border: 4px solid var(--white); background: var(--badge); }

  /* As seen on */
  .press-band { left: 0; top: 700px; width: 1200px; height: 100px; background: var(--navy);
                display: flex; align-items: center; justify-content: center; gap: 22px; color: var(--silver); font-size: 22px; }
  .press-band .brand-name { font-family: "Cormorant Garamond", Georgia, serif; font-size: 28px; }

  /* Feature rows */
  .feature-title { height: 99px; background: var(--navy); color: var(--silver); font-size: 31px;
                   display: flex; align-items: center; justify-content: center; letter-spacing: 0.5px; }
  .feature-copy { font-size: 21.6px; line-height: 26.2px; color: var(--ink); white-space: nowrap; }
  .feature-copy .line { display: block; }
  .feature-copy.justified .line { text-align: justify; text-align-last: justify; white-space: normal; }
  .feature-copy.justified .line.last { text-align-last: left; }

  /* Video */
  .video-frame { left: 0; top: 2100px; width: 1200px; height: 450px;
                 background:
                   radial-gradient(ellipse 300px 200px at 1000px 250px, rgba(230,226,220,0.35), transparent 70%),
                   radial-gradient(ellipse 380px 160px at 420px 330px, rgba(205,200,205,0.35), transparent 70%),
                   linear-gradient(180deg, #3d4a40 0%, #4f5548 40%, #8a8680 62%, #7a4a48 85%, #5a2f33 100%); }
  .video-title { left: 250px; top: 2056px; width: 700px; height: 99px; background: var(--navy); color: var(--silver);
                 font-size: 21.5px; line-height: 27px; text-align: center; display: flex; align-items: center; justify-content: center; }
  .play-btn { left: 546px; top: 2268px; }

  /* Pricing */
  .pricing-title { left: 0; top: 2586px; width: 1200px; text-align: center; font-size: 30px; font-weight: 400; color: var(--ink); }
  .price-card { background: var(--white); box-shadow: 0 2px 14px var(--grey-shadow); }
  .price-tag { background: var(--navy); color: var(--silver); border-radius: 6px; font-size: 19.5px; line-height: 23px;
               text-align: center; display: flex; align-items: center; justify-content: center; }
  .price-tag.featured { font-size: 21.5px; line-height: 26px; }
  .price-list { list-style: none; font-size: 15.5px; line-height: 18.5px; color: var(--ink); }
  .price-list li { position: relative; margin-bottom: 6.5px; }
  .price-list li::before { content: ""; position: absolute; left: -20px; top: 5px; width: 8px; height: 8px; border-radius: 50%; background: var(--ink); }
  .book-btn { left: 502px; top: 2959px; width: 195px; height: 49px; border-radius: 25px; background: var(--navy);
              color: var(--silver); font-size: 22px; display: flex; align-items: center; justify-content: center; }
</style>
</head>
<body>

<header class="site-header abs">
  <div class="brand abs"><span class="brand-dot"></span>Ridgeline Picnics</div>
  <nav class="main-nav abs">
    <a href="#" class="is-active">HOME</a>
    <a href="#">ABOUT</a>
    <a href="#">LOCATIONS</a>
    <a href="#">PRICING</a>
    <a href="#">FAQ</a>
    <a href="#">CONTACT</a>
  </nav>
</header>

<section class="hero abs" role="img" aria-label="Couple sipping red wine at a luxury cliff-top picnic overlooking mountain valleys at dusk"></section>
<h1 class="hero-title abs">SHARE AN UNFORGETTABLE MOMENT</h1>
<p class="hero-sub abs">Luxury picnics at breathtaking locations</p>
<div class="hero-btn abs">BOOK YOUR PICNIC</div>
<div class="safe-badge abs" role="img" aria-label="Safety certification badge"></div>

<div class="press-band abs"><span>As Seen On</span><span class="brand-name">Ridgeline Picnics</span></div>

<!-- Bliss -->
<div class="abs" style="left:50px;top:850px;width:550px;height:349px;background:radial-gradient(ellipse 200px 120px at 380px 300px,rgba(230,228,236,0.5),transparent 70%),linear-gradient(180deg,#8e98a6 0%,#56685e 40%,#3f4a3a 65%,#b8b4bc 85%,#8a6a74 100%);" role="img" aria-label="Couple standing at a cliff edge beside a picnic setup with cushions and lanterns"></div>
<div class="feature-title abs" style="left:550px;top:876px;width:400px;">BLISS</div>
<p class="feature-copy justified abs" style="left:624px;top:1000px;width:526px;">
  <span class="line">Enjoy true quality time with your partner, friends or</span>
  <span class="line">family. We help you create the perfect atmosphere to</span>
  <span class="line">celebrate a special moment in your life or to simply</span>
  <span class="line">spoil yourself! Our picnics are a unique and</span>
  <span class="line last">memorable experience that everyone loves.</span>
</p>

<!-- Unwind -->
<div class="abs" style="left:601px;top:1249px;width:550px;height:348px;background:radial-gradient(ellipse 180px 120px at 200px 230px,rgba(40,70,50,0.55),transparent 70%),linear-gradient(180deg,#3b4634 0%,#6a6c64 35%,#7a7a74 55%,#3a4a5a 80%,#c98a8e 100%);" role="img" aria-label="Couple relaxing together on cushions on a rock platform"></div>
<div class="feature-title abs" style="left:252px;top:1274px;width:400px;">UNWIND</div>
<p class="feature-copy abs" style="left:50px;top:1402px;">
  <span class="line">Sit back and be pampered! We do everything for you</span>
  <span class="line">so you can enjoy a stress free experience. You will</span>
  <span class="line">also discover the Blue Mountains like you never have</span>
  <span class="line">before! Each of our picnic spots are absolutely</span>
  <span class="line">stunning and also very private.</span>
</p>

<!-- Indulge -->
<div class="abs" style="left:52px;top:1649px;width:549px;height:366px;background:radial-gradient(ellipse 170px 80px at 320px 230px,rgba(190,150,100,0.6),transparent 70%),linear-gradient(160deg,#2a2a34 0%,#7a1a22 30%,#8f2a2c 55%,#9a3a30 70%,#7a1a22 100%);" role="img" aria-label="Grazing platter with cheeses, berries and nuts on a red patterned rug"></div>
<div class="feature-title abs" style="left:550px;top:1676px;width:400px;">INDULGE</div>
<p class="feature-copy abs" style="left:624px;top:1800px;">
  <span class="line">Our delicious picnics will have your mouth watering!</span>
  <span class="line">You can design your own picnic by choosing from our</span>
  <span class="line">extensive menu along with 2 choices of your favourite</span>
  <span class="line">alcoholic &amp; non-alcoholic beverages. We cater for all</span>
  <span class="line">dietary requirements and also have a BYO option.</span>
</p>

<!-- Video -->
<div class="video-frame abs" role="img" aria-label="Video still of a picnic setup with cushions, lantern and floral table overlooking a valley"></div>
<svg class="play-btn abs" width="108" height="108" viewBox="0 0 108 108" aria-hidden="true">
  <circle cx="54" cy="54" r="54" fill="rgba(70,70,70,0.55)"/>
  <path d="M42 34 L76 54 L42 74 Z" fill="rgba(110,110,110,0.7)"/>
</svg>
<div class="video-title abs">DISCOVER EXACTLY HOW OUR PICNICS WORK IN<br>ONLY 90 SECONDS!</div>

<!-- Pricing -->
<h2 class="pricing-title abs">PRICING</h2>

<div class="price-card abs" style="left:52px;top:2748px;width:368px;height:258px;"></div>
<div class="price-card abs" style="left:776px;top:2748px;width:374px;height:258px;"></div>
<div class="price-card abs" style="left:424px;top:2706px;width:350px;height:332px;"></div>

<div class="price-tag abs" style="left:144px;top:2710px;width:186px;height:77px;">BYO Picnic<br>$200 + GST</div>
<div class="price-tag featured abs" style="left:500px;top:2659px;width:200px;height:99px;">Gourmet Picnic<br>$350 + GST</div>
<div class="price-tag abs" style="left:868px;top:2710px;width:188px;height:77px;">Proposal Picnic<br>$450 + GST</div>

<ul class="price-list abs" style="left:120px;top:2806px;width:270px;">
  <li>Hire, transport and setup of picnic equipment</li>
  <li>Directions to ‘secret’ location</li>
  <li>Still or sparkling water cooled on ice with glassware</li>
  <li>BYO additional food &amp; beverages</li>
  <li>2 hour picnic</li>
  <li>Cleaning and pack up</li>
</ul>

<ul class="price-list abs" style="left:475px;top:2784px;width:290px;">
  <li>Everything in the BYO Picnic</li>
  <li>Design your own gourmet grazing platter</li>
  <li>Choose 2 types of complimentary beverages</li>
  <li>Delivery of the food and beverages to the picnic spot</li>
  <li>Matching glassware and cutlery</li>
</ul>
<div class="book-btn abs">BOOK NOW</div>

<ul class="price-list abs" style="left:816px;top:2806px;width:300px;">
  <li>Everything in the Gourmet Picnic</li>
  <li>1 on 1 VIP treatment</li>
  <li>Local suggestions for accommodation, activites, restaurants etc</li>
  <li>Assistance with any requests</li>
  <li>Directions to location prior to the picnic</li>
  <li>Anything else needed for a successful proposal</li>
</ul>

</body>
</html>
```